MRT Property - Business Cards

Looking for a business card & general letterhead, signage etc design for our new logo.

Colours:
000a20
0056a2
00b5ef
0088ce
68cef2

Fonts:
Poppins
Karla

Please keep look and feel of new brand - example in the zip package I sent.

```html
<!DOCTYPE html>
<html lang="en">
<head>
<meta charset="utf-8">
<title>MRT Property – Business Cards</title>
<link href="https://fonts.googleapis.com/css2?family=Montserrat:wght@400;500;700&display=swap" rel="stylesheet">
<style>
  :root {
    --stage: #2f2a27;
    --card: #0c1224;
    --card-edge: #060a16;
    --brand-deep: #0056a2;
    --brand-mid: #0088ce;
    --brand-bright: #00b5ef;
    --brand-light: #68cef2;
    --ink: #e8ecf4;
  }
  * { box-sizing: border-box; margin: 0; padding: 0; }
  html, body { width: 1200px; height: 786px; overflow: hidden; }
  body {
    background: var(--stage);
    font-family: "Montserrat", sans-serif;
    position: relative;
  }
  .card {
    position: absolute;
    width: 540px;
    height: 309px;
    background: var(--card);
    border-radius: 18px;
    box-shadow: 0 3px 0 var(--card-edge), 0 18px 40px rgba(0,0,0,.45);
    overflow: hidden;
  }
  .card--front { left: 40px; top: 238px; }
  .card--back  { left: 620px; top: 238px; }

  .brand-name {
    color: var(--brand-mid);
    font-weight: 700;
    letter-spacing: .5px;
    white-space: nowrap;
  }
  .card--front .brand-name {
    position: absolute; left: 34px; top: 30px; font-size: 34px; line-height: 1.1;
  }
  .card--back .brand-name {
    position: absolute; left: 0; right: 0; top: 50%;
    transform: translateY(-50%);
    text-align: center; font-size: 52px; line-height: 1.1;
  }

  .contact-block {
    position: absolute; left: 34px; bottom: 26px;
    color: var(--ink);
  }
  .accent-bar {
    position: absolute; left: -34px; top: 30px;
    width: 4px; height: 28px; background: var(--brand-bright);
  }
  .person-name { color: var(--brand-bright); font-size: 21px; font-weight: 700; line-height: 1.1; }
  .person-role { font-size: 12px; line-height: 1.3; margin-top: 2px; }
  .address { font-size: 12.5px; line-height: 1.3; margin-top: 12px; }
  .contact-list { list-style: none; margin-top: 9px; font-size: 12.5px; }
  .contact-list li { display: flex; align-items: center; gap: 9px; line-height: 1.45; }
  .contact-list svg { width: 11px; height: 11px; fill: var(--brand-light); flex: none; }
</style>
</head>
<body>
  <section class="card card--front" aria-label="Business card front">
    <div class="brand-name">MRT Property</div>
    <div class="contact-block">
      <span class="accent-bar"></span>
      <p class="person-name">Lena Whitcombe</p>
      <p class="person-role">Owner</p>
      <p class="address">48 Harbor View Road, Suite 210<br>Ashford, PA 19003</p>
      <ul class="contact-list">
        <li>
          <svg viewBox="0 0 12 12" aria-hidden="true"><path d="M2.5 1h2l1 3-1.3 1a6 6 0 0 0 2.8 2.8L8 6.5l3 1v2c0 .8-.7 1.5-1.5 1.5A9 9 0 0 1 1 2.5C1 1.7 1.7 1 2.5 1z"/></svg>
          215-555-0142
        </li>
        <li>
          <svg viewBox="0 0 12 12" aria-hidden="true"><path d="M0 2h12v8H0z"/><path d="M1 3l5 3.5L11 3" fill="none" stroke="#0c1224" stroke-width="1"/></svg>
          info@mrtproperty.com.au
        </li>
        <li>
          <svg viewBox="0 0 12 12" aria-hidden="true"><circle cx="6" cy="6" r="5.5"/><path d="M.5 6h11M6 .5c-2.5 3-2.5 8 0 11M6 .5c2.5 3 2.5 8 0 11" fill="none" stroke="#0c1224" stroke-width=".8"/></svg>
          www.mrtproperty.com.au
        </li>
      </ul>
    </div>
  </section>

  <section class="card card--back" aria-label="Business card back">
    <div class="brand-name">MRT Property</div>
  </section>
</body>
</html>
```